Steadfast Corner Vending Needs a Promotional Flyer

Design a one page, one sided 8 1/2" x 11" flyer that can be handed out to potential customers. Please keep printing efficiencies in mind. See attached old flyers and company website (steadfastcornervend.example) for reference of services. I have also attached our current logo.

```html
<!DOCTYPE html>
<html lang="en">
<head>
<meta charset="utf-8">
<title>Steadfast Corner Vending – Flyer</title>
<link href="https://fonts.googleapis.com/css2?family=Poppins:wght@400;500;600;700;800&display=swap" rel="stylesheet">
<style>
:root{
  --navy:#13293d;
  --ink:#1c2733;
  --blue:#3fa3dc;
  --sky:#5ab4e6;
  --paper:#ffffff;
  --stage:#d8d8d8;
  --rule:#c7ced5;
}
*{box-sizing:border-box;margin:0;padding:0}
html,body{width:1200px;height:2400px;overflow:hidden;background:var(--stage);font-family:'Poppins',sans-serif;color:var(--ink)}
.flyer{position:absolute;left:50px;top:487px;width:1100px;height:1426px;background:var(--paper);overflow:hidden;box-shadow:0 6px 18px rgba(0,0,0,.18)}
.abs{position:absolute}
.hero-panel{left:491px;top:0;width:609px;height:566px;background:var(--sky)}
.hero-photo{left:541px;top:63px;width:494px;height:411px;border-radius:6px;background:linear-gradient(90deg,#2a2d31 0%,#3b3f44 46%,#d8321f 54%,#c42a18 100%)}
.brand{left:66px;top:120px;display:flex;align-items:center;gap:12px}
.brand-mark{width:34px;height:34px;background:var(--navy)}
.brand-name{font-weight:700;font-size:22px;color:var(--navy);line-height:1.1;letter-spacing:.5px}
.welcome{left:63px;top:232px;font-weight:700;font-size:24px;letter-spacing:9px;color:var(--ink)}
.title{left:61px;top:268px;font-weight:800;font-size:38px;line-height:1.05;color:var(--ink)}
.title .accent{color:var(--blue)}
.intro{left:72px;top:377px;width:400px;border-left:2px solid var(--ink);padding-left:10px;font-size:19px;line-height:1.25}
.exp-band{left:135px;top:496px;width:903px;height:74px;background:var(--navy);border-radius:0 4px 4px 0;color:#fff;font-size:16.5px;line-height:1.2;padding:6px 18px 0 30px}
.badge{left:64px;top:492px;width:80px;height:80px}
.badge-text{left:64px;top:506px;width:80px;text-align:center;color:#fff;font-weight:700;font-size:26px;line-height:1}
.badge-text small{display:block;font-size:12px;font-weight:500;letter-spacing:1px}
.why{left:62px;top:594px;font-weight:700;font-size:19px;color:var(--ink)}
.why span{color:var(--blue)}
.divider{left:543px;top:634px;width:2px;height:385px;background:#e3e7eb}
.feature{position:absolute;display:flex;gap:16px;width:450px}
.feature svg{flex:0 0 66px}
.feature h3{font-weight:600;font-size:18px;color:var(--navy);line-height:1.2}
.feature p{font-size:16px;line-height:1.2}
.services{left:61px;top:1035px;width:974px;height:253px;background:var(--navy);border-radius:18px;overflow:hidden}
.services-tab{left:0;top:0;height:40px;padding:0 30px 0 18px;background:var(--blue);color:#fff;font-weight:700;font-size:19px;letter-spacing:4.5px;line-height:40px;border-radius:18px 0 30px 0}
.service-col{position:absolute;top:60px;color:#fff;font-size:16px;line-height:1.22}
.service-col h4{color:var(--sky);font-weight:700;font-size:17.5px;letter-spacing:1px;line-height:1.2;margin-bottom:14px}
.col-sep{position:absolute;top:62px;height:170px;border-left:1.5px dashed #5b7186}
.pantry-photo{right:0;top:0;width:216px;height:253px;background:linear-gradient(135deg,#5a3a26,#8a5e3e 50%,#c9c4b8)}
.contact-label{left:61px;top:1313px;font-weight:700;font-size:19px;line-height:1.1;color:var(--ink)}
.contact-label span{color:var(--blue)}
.contact-item{position:absolute;display:flex;gap:12px;font-size:17px;line-height:1.3;align-items:center;white-space:nowrap}
.contact-item.address{align-items:flex-start}
.contact-item.address svg{margin-top:2px}
.contact-sep{left:686px;top:1312px;width:1px;height:50px;background:var(--rule)}
.web{font-weight:600;font-size:16px}
</style>
</head>
<body>
<main class="flyer">
  <div class="abs hero-panel"></div>
  <div class="abs hero-photo" role="img" aria-label="Photo of a snack vending machine beside a cold drinks vending machine"></div>

  <div class="abs brand"><div class="brand-mark"></div><div class="brand-name">STEADFAST CORNER<br>VENDING</div></div>

  <div class="abs welcome">WELCOME TO</div>
  <h1 class="abs title">STEADFAST CORNER<br><span class="accent">VENDING</span></h1>
  <p class="abs intro">Our vending machine services are designed to cater to your every craving and refreshment need, all with a touch of modern convenience.</p>

  <div class="abs exp-band">With more than 30 years of experience in the vending industry, we have the knowledge and expertise to help you find the right vending solutions for your business. We have worked with businesses of all sizes, from small startups to large corporations.</div>
  <svg class="abs badge" viewBox="0 0 80 80"><circle cx="40" cy="40" r="39" fill="var(--blue)"/><circle cx="40" cy="40" r="33" fill="none" stroke="#fff" stroke-width="1.5" stroke-dasharray="3 3"/></svg>
  <div class="abs badge-text">30+<small>YEARS</small></div>

  <h2 class="abs why">WHY CHOOSE OUR VENDING <span>MACHINE SERVICES?</span></h2>
  <div class="abs divider"></div>

  <div class="feature" style="left:60px;top:640px">
    <svg viewBox="0 0 66 66"><circle cx="33" cy="33" r="31" fill="none" stroke="var(--blue)" stroke-width="2"/><circle cx="33" cy="33" r="26" fill="var(--navy)"/><path d="M23 22v18m-4-4 4 4 4-4M43 22v18m-4-4 4 4 4-4" stroke="#fff" stroke-width="2" fill="none"/><circle cx="33" cy="40" r="6" fill="none" stroke="#fff" stroke-width="1.6"/></svg>
    <div><h3>Zero Cost to you</h3><p>We provide state-of-the-art vending machines at <b>NO COST TO YOU.</b></p></div>
  </div>
  <div class="feature" style="left:60px;top:730px">
    <svg viewBox="0 0 66 66"><circle cx="33" cy="33" r="31" fill="none" stroke="var(--blue)" stroke-width="2"/><circle cx="33" cy="33" r="26" fill="var(--navy)"/><circle cx="33" cy="33" r="17" fill="none" stroke="#fff" stroke-width="1.6" stroke-dasharray="20 4"/><text x="33" y="38" text-anchor="middle" fill="#fff" font-size="13" font-family="Poppins,sans-serif">24/7</text></svg>
    <div><h3>Convenience</h3><p>With our vending machines, your favorite snacks, drinks, and essentials are just a few steps away, available 24/7.</p></div>
  </div>
  <div class="feature" style="left:60px;top:822px">
    <svg viewBox="0 0 66 66"><circle cx="33" cy="33" r="31" fill="none" stroke="var(--blue)" stroke-width="2"/><circle cx="33" cy="33" r="26" fill="var(--navy)"/><path d="M33 22l10 5v11l-10 5-10-5V27z" fill="none" stroke="#fff" stroke-width="1.6"/><path d="M23 27l10 5 10-5M33 32v11" stroke="#fff" stroke-width="1.6" fill="none"/></svg>
    <div><h3>Variety</h3><p>We offer a wide range of snacks, beverages, and everyday essentials, including healthy options, to satisfy every palate.</p></div>
  </div>
  <div class="feature" style="left:60px;top:924px">
    <svg viewBox="0 0 66 66"><circle cx="33" cy="33" r="31" fill="none" stroke="var(--blue)" stroke-width="2"/><circle cx="33" cy="33" r="26" fill="var(--navy)"/><rect x="24" y="24" width="18" height="18" rx="3" fill="none" stroke="#fff" stroke-width="1.6"/><path d="M28 19v5m5-5v5m5-5v5M28 42v5m5-5v5m5-5v5M19 28h5m-5 5h5m-5 5h5M42 28h5m-5 5h5m-5 5h5" stroke="#fff" stroke-width="1.6"/></svg>
    <div><h3>Technology</h3><p>Our vending machines are equipped with state-of-the-art technology, making payments easy with a variety of options.</p></div>
  </div>

  <div class="feature" style="left:596px;top:637px">
    <svg viewBox="0 0 66 66"><circle cx="33" cy="33" r="31" fill="none" stroke="var(--blue)" stroke-width="2"/><circle cx="33" cy="33" r="26" fill="var(--navy)"/><path d="M33 20l11 4v8c0 8-5 12-11 14-6-2-11-6-11-14v-8z" fill="none" stroke="#fff" stroke-width="1.6"/><path d="M28 33l4 4 7-8" stroke="#fff" stroke-width="1.8" fill="none"/></svg>
    <div><h3>Reliability</h3><p>We are so passionate about being reliable that it is in our name. We are a small company that is HUGE on service.</p></div>
  </div>
  <div class="feature" style="left:596px;top:727px">
    <svg viewBox="0 0 66 66"><circle cx="33" cy="33" r="31" fill="none" stroke="var(--blue)" stroke-width="2"/><circle cx="33" cy="33" r="26" fill="var(--navy)"/><circle cx="33" cy="37" r="9" fill="none" stroke="#fff" stroke-width="1.6"/><path d="M24 23l1.5 3 3 .4-2.2 2 .6 3-2.9-1.5-2.9 1.5.6-3-2.2-2 3-.4zM42 23l1.5 3 3 .4-2.2 2 .6 3-2.9-1.5-2.9 1.5.6-3-2.2-2 3-.4z" fill="#fff"/></svg>
    <div><h3>Quality</h3><p>We stock our vending machines with high-quality, fresh products from trusted brands.</p></div>
  </div>
  <div class="feature" style="left:596px;top:822px">
    <svg viewBox="0 0 66 66"><circle cx="33" cy="33" r="31" fill="none" stroke="var(--blue)" stroke-width="2"/><circle cx="33" cy="33" r="26" fill="var(--navy)"/><circle cx="33" cy="33" r="11" fill="none" stroke="#fff" stroke-width="3" stroke-dasharray="4 3"/><circle cx="33" cy="33" r="5" fill="none" stroke="#fff" stroke-width="1.6"/></svg>
    <div><h3>Customization</h3><p>Tailor the vending machine offerings to your specific needs. We can customize our vending services to suit your preferences.</p></div>
  </div>
  <div class="feature" style="left:596px;top:925px">
    <svg viewBox="0 0 66 66"><circle cx="33" cy="33" r="31" fill="none" stroke="var(--blue)" stroke-width="2"/><circle cx="33" cy="33" r="26" fill="var(--navy)"/><path d="M23 23l20 20M43 23L23 43" stroke="#fff" stroke-width="2.4" stroke-linecap="round"/><circle cx="23" cy="23" r="3.5" fill="none" stroke="#fff" stroke-width="1.6"/><circle cx="43" cy="23" r="3.5" fill="none" stroke="#fff" stroke-width="1.6"/></svg>
    <div><h3>On-time Maintenance</h3><p>Our proactive maintenance team ensures that you always have a hassle-free experience</p></div>
  </div>

  <section class="abs services">
    <div class="abs services-tab">STEADFAST CORNER SUPERIOR SERVICE</div>
    <div class="service-col" style="left:22px;width:210px"><h4>VENDING MACHINE<br>SERVICES</h4>Our vending machine services are designed to cater to your every craving and refreshment need, all with a touch of modern convenience.</div>
    <div class="col-sep" style="left:248px"></div>
    <div class="service-col" style="left:272px;width:210px"><h4>COFFEE SERVICE</h4>At Steadfast Corner Vending, we are committed to delivering exceptional coffee and other hot beverage experiences to our customers.</div>
    <div class="col-sep" style="left:500px"></div>
    <div class="service-col" style="left:516px;width:240px"><h4>PANTRY SERVICE</h4>Elevate the break room experience in your office with a customized selection of snacks, beverages, and kitchen essentials, all conveniently accessible in your workplace pantry.</div>
    <div class="abs pantry-photo" role="img" aria-label="Photo of a stocked office pantry with wooden shelving and a drinks cooler"></div>
  </section>

  <div class="abs contact-label">CONTACT US FOR<br><span>MORE INFORMATION</span></div>
  <div class="contact-item address" style="left:300px;top:1311px">
    <svg width="20" height="22" viewBox="0 0 20 22"><path d="M10 1a8 8 0 0 0-8 8c0 6 8 12 8 12s8-6 8-12a8 8 0 0 0-8-8z" fill="var(--navy)"/><circle cx="10" cy="9" r="3" fill="#fff"/></svg>
    <div>1480 Meadowbrook Ave. Unit 12,<br>Fairview Heights, Illinois 60990, USA</div>
  </div>
  <div class="abs contact-sep"></div>
  <div class="contact-item" style="left:704px;top:1310px">
    <svg width="18" height="18" viewBox="0 0 18 18"><circle cx="9" cy="9" r="9" fill="var(--navy)"/><path d="M5.5 5c.5 3 3 6 7 7l1-1.6-2-1-1 1c-1.2-.6-2.3-1.7-2.9-2.9l1-1-1-2z" fill="#fff"/></svg>
    <div>555-014-2290</div>
  </div>
  <div class="contact-item" style="left:704px;top:1337px">
    <svg width="18" height="18" viewBox="0 0 18 18"><circle cx="9" cy="9" r="8" fill="none" stroke="var(--navy)" stroke-width="1.8"/><path d="M1 9h16M9 1c-3 3-3 13 0 16M9 1c3 3 3 13 0 16" stroke="var(--navy)" stroke-width="1.4" fill="none"/></svg>
    <div class="web">www.steadfastcornervend.example</div>
  </div>
</main>
</body>
</html>
```